New, modern business card for growing audiology practice

We need a new business card for our audiology practice. Our logo and website have recently changed (more modern) and we want our business cards to reflect this change.
We conduct hearing tests, perform earwax removals, and fit & dispense hearing aids to our patients. We are a family owned practice in which the owner is the one who works directly with the patient. I have attached logos in various formats to use, as well as two ideas I found on this website; as well as a scanned copy of our current logo. Good luck!

Industry/Entity Type

Business

Contact Information for Business Card

Company name: Tolvera Hearing Center
Provider name: Peter Wolstenby, Au.D. F/NSB
Phone number: (440) 683-5127
Address: 837 W. Lindell Ave. Brennick Falls, OH 44917
email: tolverahearing@postvane.com
website: tolverahearing.com

Colors
000000
aaaaaa
dbdbdb
cacaca
9bcb3c
afd23c
cadf82
b1b1b1

Requirements
Must have
• My card must include information in the "details" section. In the attached images, I found a few that I liked and I would like to model after - "brisky bouncin'" and "Sound Method Center".
• Must be horizontal.
• Must include logos provided. I uploaded them in various file formats and various ways.
• Must match logo font, if possible, if not, please get as close as you can.
Nice to have
• I really like the idea of having a color on one side with just the logo and company name and the contact information and provider name on the other side. I also really like the idea of having the main color dominating on the logo/company side with accent of that same color on the contact side of the card.
Should not have
• Must not be vertical.

```html
<!DOCTYPE html>
<html lang="en">
<head>
<meta charset="utf-8">
<title>Tolvera Hearing Center – Business Card</title>
<link href="https://fonts.googleapis.com/css2?family=Lato:wght@400&family=Fira+Sans+Condensed:wght@500&family=Roboto:wght@400&display=swap" rel="stylesheet">
<style>
  :root {
    --bg: #b1b1b1;
    --green: #5a9232;
    --green-light: #9bcb3c;
    --paper: #f1f1f1;
    --paper-edge: #dbdbdb;
    --ink: #1b1b1b;
    --ink-soft: #333333;
    --white: #ffffff;
  }
  * { margin: 0; padding: 0; box-sizing: border-box; }
  html, body { width: 1200px; height: 576px; overflow: hidden; }
  body { background: var(--bg); position: relative; font-family: "Roboto", sans-serif; }

  .card {
    position: absolute;
    border-radius: 12px;
    overflow: hidden;
  }
  .card-front {
    left: 80px; top: 139px; width: 486px; height: 293px;
    background: linear-gradient(180deg, #5e9836 0%, var(--green) 100%);
  }
  .card-back {
    left: 602px; top: 138px; width: 480px; height: 290px;
    background: linear-gradient(180deg, #fafafa 0%, var(--paper) 60%, #e9e9e9 100%);
  }

  .brand { position: absolute; display: flex; align-items: center; }
  .brand-dot { border-radius: 50%; flex: none; }
  .brand-name { font-family: "Lato", sans-serif; font-weight: 400; line-height: 1; }
  .brand-name .line { display: block; }

  .card-front .brand { left: 114px; top: 112px; gap: 22px; }
  .card-front .brand-dot { width: 38px; height: 38px; background: var(--white); }
  .card-front .brand-name { color: var(--white); }
  .card-front .brand-name .line-main { font-size: 42px; letter-spacing: 0.5px; }
  .card-front .brand-name .line-sub { font-size: 23px; margin-top: 6px; }

  .card-back .brand { left: 264px; top: 40px; gap: 16px; }
  .card-back .brand-dot { width: 28px; height: 28px; background: var(--green-light); }
  .card-back .brand-name { color: var(--ink); }
  .card-back .brand-name .line-main { font-size: 31px; letter-spacing: 0.4px; }
  .card-back .brand-name .line-sub { font-size: 17px; margin-top: 4px; }

  .provider { position: absolute; left: 21px; top: 44px; }
  .provider-name {
    font-family: "Fira Sans Condensed", sans-serif; font-weight: 500;
    font-size: 17px; color: var(--green); line-height: 1;
  }
  .provider-role { font-size: 12px; color: var(--ink-soft); margin-top: 10px; }

  .contact { position: absolute; left: 26px; top: 172px; list-style: none; }
  .contact li {
    display: flex; align-items: flex-start; gap: 8px;
    font-size: 13px; color: var(--ink-soft); line-height: 16.8px;
  }
  .contact svg { width: 10px; height: 10px; margin-top: 3px; flex: none; fill: var(--green); }
  .contact .address { display: block; }

  .accent-band {
    position: absolute; left: 0; bottom: 0; width: 100%; height: 10px;
    background: var(--green);
  }
</style>
</head>
<body>

  <section class="card card-front" aria-label="Card front">
    <div class="brand">
      <span class="brand-dot"></span>
      <span class="brand-name">
        <span class="line line-main">TOLVERA</span>
        <span class="line line-sub">HEARING CENTER</span>
      </span>
    </div>
  </section>

  <section class="card card-back" aria-label="Card back">
    <div class="provider">
      <p class="provider-name">Peter Wolstenby, Au.D. F/NSB</p>
      <p class="provider-role">Owner - Audiologist</p>
    </div>

    <div class="brand">
      <span class="brand-dot"></span>
      <span class="brand-name">
        <span class="line line-main">TOLVERA</span>
        <span class="line line-sub">HEARING CENTER</span>
      </span>
    </div>

    <ul class="contact">
      <li>
        <svg viewBox="0 0 10 10" aria-hidden="true"><path d="M5 0a3.6 3.6 0 0 0-3.6 3.6C1.4 6.3 5 10 5 10s3.6-3.7 3.6-6.4A3.6 3.6 0 0 0 5 0zm0 5a1.4 1.4 0 1 1 0-2.8A1.4 1.4 0 0 1 5 5z"/></svg>
        <span class="address">837 W. Lindell Ave.<br>Brennick Falls, OH 44917</span>
      </li>
      <li>
        <svg viewBox="0 0 10 10" aria-hidden="true"><path d="M1 3.2C1 2 2.5 1.2 5 1.2S9 2 9 3.2V4H7V3H3v1H1zM2 5l1.6-1.2h2.8L8 5v4H2zm3 .6A1.3 1.3 0 1 0 5 8.2a1.3 1.3 0 0 0 0-2.6z"/></svg>
        <span>(440) 683-5127</span>
      </li>
      <li>
        <svg viewBox="0 0 10 10" aria-hidden="true"><path d="M0 2h10v6H0zm1 .8v.2l4 2.6 4-2.6v-.2zM1 4v3.2h8V4L5 6.6z"/></svg>
        <span>tolverahearing@postvane.com</span>
      </li>
      <li>
        <svg viewBox="0 0 10 10" aria-hidden="true"><path d="M5 0a5 5 0 1 0 0 10A5 5 0 0 0 5 0zm3.9 4.5H7.2A8 8 0 0 0 6.5 1.3a4 4 0 0 1 2.4 3.2zM5 1c.6.7 1.1 2 1.2 3.5H3.8C3.9 3 4.4 1.7 5 1zM3.5 1.3a8 8 0 0 0-.7 3.2H1.1a4 4 0 0 1 2.4-3.2zM1.1 5.5h1.7a8 8 0 0 0 .7 3.2 4 4 0 0 1-2.4-3.2zM5 9c-.6-.7-1.1-2-1.2-3.5h2.4C6.1 7 5.6 8.3 5 9zm1.5-.3a8 8 0 0 0 .7-3.2h1.7a4 4 0 0 1-2.4 3.2z"/></svg>
        <span>www.tolverahearing.com</span>
      </li>
    </ul>

    <div class="accent-band"></div>
  </section>

</body>
</html>
```